Corporate Design für Lunavello - innovatives Unternehmen im Bereich App-Entwicklung und Kultur
Zielgruppe
Gegenstand des Unternehmens ist:
- Entwurf, Entwicklung und Vermarktung von Soziale Netzwerk-Apps für Unternehmen im Kultursektor und für einzelne Kunstprojekte
- Beratung von Kultureinrichtungen
- Technische Umsetzung als Dienstleister von digitalen Apps, Websites, Softwares für den Kulturbereich
- Entwicklung und Erstellung von digitalen Diensten im Kulturbereich
- Entwicklung von Augmented Reality und 3D Technologien für mobile Devices
- Ausbildung im Bereich Kultur und Kreativität
- Erbringung von Dienstleistungen im Media- und Marketingbereich
- Organisation von Kulturveranstaltungen
Zielgruppe sind insbesondere Kreative und Kultureinrichtungen.
www.lunavello.eu
Aufgabenstellung
bitte die Farbe der Website NICHT berücksichtigen. Wir wollen sowieso die Website ändern.
bitte keine Fernseher, Kameras, Videokameras im Logo. Wir bevorzugen etwas abstraktes.
Danke und viel Spass!!

```html
<!DOCTYPE html>
<html lang="de">
<head>
<meta charset="utf-8">
<title>Lunavello – Geschäftsausstattung</title>
<link rel="stylesheet" href="https://fonts.googleapis.com/css2?family=Open+Sans:wght@400;600;700&display=swap">
<style>
  :root {
    --lime: #9fc31a;
    --lime-soft: rgba(255,255,255,0.18);
    --ink: #4a4a4a;
    --grey: #5b5b5b;
    --rule: #9a9a9a;
    --paper: #ffffff;
    --backdrop: #d9d9d7;
  }
  * { margin: 0; padding: 0; box-sizing: border-box; }
  html, body { width: 1200px; height: 1198px; overflow: hidden; }
  body {
    background: var(--backdrop);
    font-family: "Open Sans", Arial, sans-serif;
    color: var(--ink);
    position: relative;
  }
  .sheet {
    position: absolute; left: 74px; top: 78px; width: 742px; height: 1046px;
    background: var(--paper);
    box-shadow: 0 2px 8px rgba(0,0,0,0.18);
  }
  .wordmark { font-weight: 600; letter-spacing: 0.04em; line-height: 1; }
  .sheet-logo {
    position: absolute; left: 90px; top: 90px;
    display: flex; align-items: center; gap: 10px;
  }
  .sheet-logo .mark { width: 22px; height: 22px; background: var(--lime); }
  .sheet-logo .wordmark { font-size: 26px; color: var(--grey); }
  .sheet-rule {
    position: absolute; left: 172px; top: 308px; width: 1px; height: 456px;
    background: var(--rule);
  }
  .letter {
    position: absolute; left: 197px; top: 436px; width: 500px;
    font-size: 10.8px; line-height: 15px;
  }
  .letter p { margin-bottom: 15px; }
  .letter .closing { margin-top: 30px; }
  .sender {
    position: absolute; left: 0; top: 820px; width: 176px;
    text-align: right; font-size: 10px; line-height: 13.5px;
  }
  .sender .icon { display: inline-block; margin-bottom: 6px; }
  .sender p { margin-bottom: 13px; }
  .sender b { font-weight: 700; }
  .sheet-band {
    position: absolute; left: 0; bottom: 0; width: 100%; height: 26px;
    background: var(--lime);
  }
  .card {
    position: absolute; left: 784px; width: 308px; height: 200px;
    box-shadow: 0 2px 8px rgba(0,0,0,0.2);
    overflow: hidden;
  }
  .card-front { top: 324px; background: var(--lime); }
  .card-front .ghost {
    position: absolute; left: 24px; top: 40px; width: 150px; height: 150px;
    background: var(--lime-soft);
  }
  .card-front .card-logo {
    position: absolute; left: 62px; top: 82px;
    display: flex; align-items: center; gap: 10px;
  }
  .card-front .mark { width: 20px; height: 20px; background: #fff; }
  .card-front .wordmark { font-size: 24px; color: var(--grey); }
  .card-back { top: 566px; height: 202px; background: var(--paper); }
  .card-back .name {
    position: absolute; top: 53px; width: 100%; text-align: center;
    color: var(--lime); font-weight: 700; font-size: 12px;
  }
  .card-back .role {
    position: absolute; top: 70px; width: 100%; text-align: center;
    font-weight: 700; font-size: 8.5px;
  }
  .card-back .col {
    position: absolute; top: 114px; font-size: 9.6px; line-height: 14px;
  }
  .card-back .col-contact { left: 24px; }
  .card-back .col-address { left: 199px; }
  .card-back .col b { font-weight: 700; }
  .card-back .stripe {
    position: absolute; left: 0; bottom: 0; width: 100%; height: 6px;
    background: var(--lime);
  }
  .standalone-logo {
    position: absolute; left: 872px; top: 1010px;
    display: flex; align-items: center; gap: 14px;
  }
  .standalone-logo .mark { width: 34px; height: 34px; background: #666; }
  .standalone-logo .wordmark { font-size: 40px; color: #666; }
</style>
</head>
<body>

<section class="sheet" aria-label="Briefbogen">
  <div class="sheet-logo">
    <span class="mark"></span>
    <span class="wordmark">lunavello</span>
  </div>

  <div class="sheet-rule"></div>

  <div class="letter">
    <p>Sehr geehrter Herr Peter Lindqvist,</p>
    <p>Sed ut perspiciatis unde omnis iste natus error sit voluptatem accusantium doloremque laudantium, totam rem aperiam, eaque ipsa quae ab illo inventore veritatis et quasi architecto beatae vitae dicta sunt explicabo.</p>
    <p>Nemo enim ipsam voluptatem quia voluptas sit aspernatur aut odit aut fugit, sed quia consequuntur magni dolores eos qui ratione voluptatem sequi nesciunt. Neque porro quisquam est, qui dolorem ipsum quia dolor sit amet, consectetur, adipisci velit, sed quia non numquam eius modi tempora incidunt ut labore et dolore magnam aliquam quaerat voluptatem.</p>
    <p>Ut enim ad minima veniam, quis nostrum exercitationem ullam corporis suscipit laboriosam, nisi ut aliquid ex ea commodi consequatur? Quis autem vel eum iure reprehenderit qui in ea voluptate velit esse quam nihil molestiae consequatur, vel illum qui dolorem eum fugiat quo voluptas nulla pariatur?</p>
    <p class="closing">Mit freundlichen Grüßen</p>
    <p>Jonas Feldhuber</p>
  </div>

  <div class="sender">
    <svg class="icon" width="36" height="28" viewBox="0 0 36 28" aria-hidden="true">
      <rect x="6" y="6" width="20" height="14" fill="#9fc31a"/>
      <polyline points="6,6 16,14 26,6" fill="none" stroke="#fff" stroke-width="1.5"/>
      <rect x="27" y="14" width="3" height="11" fill="#9fc31a"/>
      <rect x="23" y="18" width="11" height="3" fill="#9fc31a"/>
    </svg>
    <p><b>lunavello</b><br>Lindenweg 7<br>54321 Talheim</p>
    <p>Phone 09876 - 54321-0<br>Fax 09876 - 54321-1</p>
    <p>info@beispielnetz.ch<br>www.beispielnetz.ch</p>
  </div>

  <div class="sheet-band"></div>
</section>

<section class="card card-front" aria-label="Visitenkarte Vorderseite">
  <div class="ghost"></div>
  <div class="card-logo">
    <span class="mark"></span>
    <span class="wordmark">lunavello</span>
  </div>
</section>

<section class="card card-back" aria-label="Visitenkarte Rückseite">
  <div class="name">JONAS FELDHUBER</div>
  <div class="role">Creative Director</div>
  <div class="col col-contact">
    Phone 09876 - 54321-0<br>
    Fax 09876 - 54321-1<br>
    Mail: info@lunavello.eu<br>
    Web: www.lunavello.eu
  </div>
  <div class="col col-address">
    <b>lunavello</b><br>
    Lindenweg 7<br>
    54321 Talheim<br>
    Deutschland
  </div>
  <div class="stripe"></div>
</section>

<div class="standalone-logo" aria-label="Lunavello">
  <span class="mark"></span>
  <span class="wordmark">lunavello</span>
</div>

</body>
</html>
```